Brellwick Partners, LLC Stationary

Brellwick Partners, LLC is a new financial planning and consulting company. We are looking for designs on business cards, letterhead, envelopes, and anything else that would be useful. Our preference for business card design is two sided. We are looking for a professional and clean look with incorporating the logo and patriotic feel. Thank you to all who participate and good luck!

```html
<!DOCTYPE html>
<html lang="en">
<head>
<meta charset="utf-8">
<title>Brellwick Partners, LLC – Business Card</title>
<link rel="stylesheet" href="https://fonts.googleapis.com/css2?family=Arimo:wght@400;700&display=swap">
<style>
  :root {
    --navy: #123a6b;
    --navy-deep: #0b2a52;
    --red: #d9333f;
    --ink: #3a3a3a;
    --muted: #6a6a6a;
    --paper: #ffffff;
    --paper-shade: #e9eaec;
    --backdrop: #e4e2dd;
  }
  * { box-sizing: border-box; margin: 0; padding: 0; }
  html, body { width: 1200px; height: 950px; overflow: hidden; }
  body {
    background: var(--backdrop);
    font-family: "Arimo", Arial, sans-serif;
    display: flex; flex-direction: column; align-items: center; justify-content: center;
    gap: 60px;
  }
  .card {
    position: relative;
    width: 595px; height: 340px;
    border-radius: 4px;
    overflow: hidden;
    box-shadow: 0 10px 24px rgba(0,0,0,.18);
  }

  /* Back */
  .card-back {
    background: linear-gradient(135deg, var(--navy) 0%, var(--navy-deep) 100%);
    color: var(--paper);
    display: flex; flex-direction: column; align-items: center; justify-content: center;
  }
  .card-back .brand-name { color: var(--paper); font-size: 40px; }
  .card-back .brand-tagline { color: #c9d3e2; border-top-color: rgba(255,255,255,.5); }
  .card-back .web {
    position: absolute; bottom: 34px; left: 0; right: 0;
    text-align: center; font-size: 17px; letter-spacing: 4px; color: #dfe6f0;
  }

  /* Brand block */
  .brand { display: flex; flex-direction: column; align-items: flex-start; }
  .card-back .brand { align-items: center; }
  .brand-row { display: flex; align-items: center; gap: 12px; }
  .brand-mark { width: 22px; height: 22px; background: var(--red); }
  .brand-name {
    font-weight: 700; font-size: 28px; letter-spacing: 1px;
    color: var(--navy); text-transform: uppercase; line-height: 1;
  }
  .brand-tagline {
    margin-top: 6px; padding-top: 4px;
    border-top: 1px solid var(--red);
    font-size: 9px; letter-spacing: 2px; text-transform: uppercase;
    color: var(--muted);
  }

  /* Front */
  .card-front {
    background: linear-gradient(180deg, var(--paper) 0%, var(--paper) 70%, var(--paper-shade) 100%);
    color: var(--ink);
  }
  .card-front .brand { position: absolute; top: 36px; left: 36px; }
  .name-band {
    position: absolute; top: 118px; left: 0; right: 0; height: 54px;
    background: var(--navy);
    color: var(--paper);
    padding: 8px 36px;
  }
  .person-name { font-weight: 700; font-size: 18px; letter-spacing: .5px; text-transform: uppercase; }
  .person-title { font-size: 14px; text-transform: uppercase; margin-top: 3px; }
  .contact { position: absolute; top: 196px; left: 36px; list-style: none; font-size: 15px; color: var(--muted); }
  .contact li { display: flex; align-items: center; gap: 8px; height: 21px; }
  .contact svg { width: 14px; height: 14px; fill: var(--navy); }
  .address {
    position: absolute; right: 36px; bottom: 28px;
    text-align: right; font-size: 16px; color: var(--muted); line-height: 1.45;
  }
  .address .web { letter-spacing: 3px; }
</style>
</head>
<body>

  <section class="card card-back" aria-label="Business card, back">
    <div class="brand">
      <div class="brand-row">
        <span class="brand-mark" aria-hidden="true"></span>
        <span class="brand-name">Brellwick Partners, LLC</span>
      </div>
      <div class="brand-tagline">Financial Planning and Consulting</div>
    </div>
    <div class="web">www.brellwick.com</div>
  </section>

  <section class="card card-front" aria-label="Business card, front">
    <div class="brand">
      <div class="brand-row">
        <span class="brand-mark" aria-hidden="true"></span>
        <span class="brand-name">Brellwick Partners, LLC</span>
      </div>
      <div class="brand-tagline">Financial Planning and Consulting</div>
    </div>

    <div class="name-band">
      <div class="person-name">Marcus Hale</div>
      <div class="person-title">President</div>
    </div>

    <ul class="contact">
      <li>
        <svg viewBox="0 0 24 24" aria-hidden="true"><path d="M6.6 10.8a15.1 15.1 0 0 0 6.6 6.6l2.2-2.2a1 1 0 0 1 1-.25 11.4 11.4 0 0 0 3.6.57 1 1 0 0 1 1 1V20a1 1 0 0 1-1 1A17 17 0 0 1 3 4a1 1 0 0 1 1-1h3.5a1 1 0 0 1 1 1c0 1.25.2 2.45.57 3.57a1 1 0 0 1-.25 1z"/></svg>
        555 0142 7781
      </li>
      <li>
        <svg viewBox="0 0 24 24" aria-hidden="true"><path d="M6 3h10v5H6zM4 9h16a2 2 0 0 1 2 2v6h-4v4H6v-4H2v-6a2 2 0 0 1 2-2zm4 7v3h8v-3z"/></svg>
        555 0198 3364
      </li>
      <li>
        <svg viewBox="0 0 24 24" aria-hidden="true"><path d="M2 5h20v14H2zm2 2v.5l8 5 8-5V7z"/></svg>
        marcus@brellwick.com
      </li>
    </ul>

    <div class="address">
      4127 Harrowgate Lane<br>
      Elm Ridge, NY 11420<br>
      <span class="web">www.brellwick.com</span>
    </div>
  </section>

</body>
</html>
```